Web Banner Ads for Velorin Baby Monitor

Velorin is a top selling security camera company that is currently #1 best sellers on several categories on Quillmart. We have just released a new Velorin Baby Monitor and are in need of web banner ads for the Velorin baby Monitor that will be placed on Quillmart Promotion Networks that will be displayed throughout Quillmart.

We would like for the designer to provide Ads that can display some of the features and functionality of the baby monitor and camera, while still maintaining a modern, slick and simple style. The banners can have a tag line but should share the same theme of watching over your loved one.

There will need to be several different sizes that must be exact and adhere strictly to the guidelines below. If the creatives are off by even a little bit or are over the file size they will be kicked back. I have submitted a sample of another add for one of our Wifi cameras as well.

Please have a look at the listing below for more information on the product.

https://www.quillmart-shop.example/Velorin-Monitor-Night-Vision-Camera/dp/K58PZ3RT4M

Target Market(s)

Quillmart, online shoppers, parents, new parents, mothers, home owners, pet owners.

Industry/Entity Type

Baby Care

Number of Pages Required

1 page

Requirements
Must have
• All of the dimensions required in the attached files. We will also need the creatives submitted as JPEGs adhering to the exact size and dimensions as well as the PSD files.

```html
<!DOCTYPE html>
<html lang="en">
<head>
<meta charset="utf-8">
<title>Velorin Baby Monitor – Web Banner 1200×111</title>
<link rel="stylesheet" href="https://fonts.googleapis.com/css2?family=Oswald:wght@600&family=Roboto:wght@400;500&family=Montserrat:wght@400&display=swap">
<style>
  :root {
    --sky: #37c3ee;
    --sky-light: #5fd0f3;
    --frame: #2fb7e6;
    --navy: #1c2550;
    --ink: #22284a;
    --button: #3cbde9;
    --white: #ffffff;
    --photo-light: #f6f8fb;
    --photo-mid: #e3ebf5;
    --photo-blue: #b3cdee;
    --device: #f1f2f4;
    --device-shade: #dadde0;
  }
  * { margin: 0; padding: 0; box-sizing: border-box; }
  html, body { width: 1200px; height: 111px; overflow: hidden; background: var(--white); }
  .banner {
    position: relative;
    width: 1200px;
    height: 111px;
    overflow: hidden;
    background: var(--white);
    border: 2px solid var(--frame);
    font-family: "Roboto", Arial, sans-serif;
  }
  .brand-panel {
    position: absolute;
    left: 0;
    top: 0;
    width: 380px;
    height: 111px;
    z-index: 1;
  }
  .brand {
    position: absolute;
    left: 28px;
    top: 38px;
    display: flex;
    align-items: center;
    gap: 20px;
    color: var(--white);
    z-index: 2;
  }
  .brand-mark {
    width: 32px;
    height: 32px;
    border: 3px solid var(--white);
    border-radius: 50%;
  }
  .brand-name {
    font-family: "Montserrat", Arial, sans-serif;
    font-weight: 400;
    font-size: 27px;
    letter-spacing: 12px;
    line-height: 1;
  }
  .hero-photo {
    position: absolute;
    left: 600px;
    top: 0;
    width: 400px;
    height: 107px;
    background:
      radial-gradient(ellipse 100px 42px at 150px 48px, var(--photo-blue), transparent 70%),
      linear-gradient(180deg, var(--photo-light) 0%, var(--photo-mid) 100%);
    clip-path: polygon(60px 0, 100% 0, 100% 100%, 0 100%);
    z-index: 1;
  }
  .product-photo {
    position: absolute;
    left: 990px;
    top: 8px;
    width: 180px;
    height: 96px;
    border-radius: 10px;
    background: linear-gradient(180deg, var(--device) 0%, var(--device-shade) 100%);
    z-index: 1;
  }
  .message {
    position: absolute;
    left: 345px;
    top: 0;
    width: 300px;
    height: 107px;
    text-align: center;
    color: var(--ink);
    z-index: 3;
    white-space: nowrap;
  }
  .tagline {
    position: absolute;
    left: 0;
    right: 0;
    top: 18px;
    font-family: "Oswald", "Arial Narrow", sans-serif;
    font-weight: 600;
    font-size: 26px;
    line-height: 30px;
    color: var(--navy);
    text-transform: uppercase;
  }
  .feature {
    position: absolute;
    left: 0;
    right: 0;
    font-size: 11px;
    font-weight: 400;
    line-height: 14px;
    text-transform: uppercase;
  }
  .feature-camera { top: 57px; }
  .feature-night { top: 76px; }
  .shop-button {
    position: absolute;
    left: 643px;
    top: 46px;
    width: 99px;
    height: 28px;
    border-radius: 14px;
    background: var(--button);
    color: var(--white);
    font-size: 12.5px;
    font-weight: 500;
    line-height: 28px;
    text-align: center;
    text-decoration: none;
    text-transform: uppercase;
    z-index: 4;
  }
  .ad-code {
    position: absolute;
    right: 6px;
    bottom: 4px;
    font-size: 7px;
    color: var(--ink);
    z-index: 4;
  }
</style>
</head>
<body>
  <div class="banner">
    <svg class="brand-panel" viewBox="0 0 380 111" aria-hidden="true">
      <defs>
        <linearGradient id="panel-fill" x1="0" y1="0" x2="0" y2="1">
          <stop offset="0" stop-color="#5fd0f3"/>
          <stop offset="1" stop-color="#37c3ee"/>
        </linearGradient>
      </defs>
      <polygon points="0,0 312,0 368,111 0,111" fill="url(#panel-fill)"/>
    </svg>

    <div class="brand">
      <span class="brand-mark"></span>
      <span class="brand-name">VELORIN</span>
    </div>

    <div class="hero-photo" role="img" aria-label="Photo of a sleeping baby in blue pyjamas hugging a soft toy on white bedding"></div>
    <div class="product-photo" role="img" aria-label="Photo of the white Velorin pan/tilt camera with its handheld video monitor"></div>

    <div class="message">
      <h1 class="tagline">Be there even if you're not</h1>
      <p class="feature feature-camera">Pan/Tilt baby monitor and camera</p>
      <p class="feature feature-night">Pan/Tilt baby monitor with night vision</p>
    </div>

    <a class="shop-button" href="https://www.quillmart-shop.example/Velorin-Monitor-Night-Vision-Camera/dp/K58PZ3RT4M">Shop now</a>

    <span class="ad-code">C7</span>
  </div>
</body>
</html>
```